K7 Electrical Services Ltd Web design

I require a web site for my new electrical contracting company. We are customer service orientated. Offering high value electrical installations, design and maintenance. Focused on custom residential and commercial upgrading. Lighting design and application are paramount in our company's services. Industry leading product use and integration are always on the forefront with our customer client services. As well as energy efficiency.

Target Market(s)

Homebuilders, General Contractors, Property management companies, clients, individuals,

Industry/Entity Type

Electric Company

Coding

Coded - Design and coding required

Number of Pages Required

3 page

Requirements
Must have
• Classic, modern, edgy but not trendy . Appeals to the masse.
• 3 page
• home page
• about page
• gallery page
• ability to contact from the webiste
Nice to have
• open to all types of designs that are relative to the construction industry.
• Black, Grey, metallic ice blue and deep purple colours from the logo.
Should not have
• anything cheesy with cartoon light bulb images.

```html
<!DOCTYPE html>
<html lang="en">
<head>
<meta charset="utf-8">
<title>K7 Electrical Services Ltd</title>
<link href="https://fonts.googleapis.com/css2?family=Montserrat:wght@400;500;600;700&family=Lato:wght@400;700&display=swap" rel="stylesheet">
<style>
:root{
  --purple:#5b2d8e;
  --purple-deep:#2e0e5a;
  --purple-light:#9b63c6;
  --orange:#ff8a00;
  --grey-panel:#5f5f63;
  --grey-bg:#e6e6e6;
  --text:#555;
  --dark:#2b2b2b;
  --darker:#1f1f1f;
  --white:#fff;
}
*{margin:0;padding:0;box-sizing:border-box}
html,body{width:1200px;height:3066px;overflow:hidden}
body{font-family:'Lato',sans-serif;color:var(--text);background:var(--white);position:relative}
section,header,footer{position:absolute;left:0;width:1200px}
.brand{font-family:'Montserrat',sans-serif;font-weight:700;color:var(--purple);font-size:24px;line-height:28px;letter-spacing:1px;text-transform:uppercase}
/* header */
.site-header{top:0;height:119px}
.site-header .brand{position:absolute;left:119px;top:22px}
.phone{position:absolute;right:123px;top:24px;font-size:20px;color:#666;display:flex;align-items:center;gap:8px}
.main-nav{position:absolute;right:123px;top:64px;display:flex;gap:8px;font-family:'Montserrat',sans-serif;font-weight:600;font-size:15px;color:#333}
.main-nav a{padding:9px 14px;text-decoration:none;color:inherit}
.main-nav a.active{background:var(--purple);color:var(--white)}
/* hero */
.hero{top:119px;height:531px;background:linear-gradient(100deg,#5b6a7c 0%,#9aa3ad 40%,#c9ccd0 70%,#b7b9bc 100%);text-align:center;color:var(--white)}
.hero h1{font-family:'Montserrat',sans-serif;font-weight:600;font-size:39px;letter-spacing:2px;margin-top:186px;line-height:44px}
.hero h2{font-family:'Montserrat',sans-serif;font-weight:600;font-size:31px;letter-spacing:2px;line-height:36px}
.btn-orange{display:inline-block;margin-top:28px;background:var(--orange);color:var(--white);font-family:'Montserrat',sans-serif;font-weight:600;font-size:15px;width:190px;height:47px;line-height:47px}
.dots{position:absolute;left:0;right:0;top:490px;display:flex;justify-content:center;gap:10px}
.dots span{width:14px;height:14px;border-radius:50%;background:var(--white)}
.dots span:first-child{background:none;border:2px solid var(--white)}
/* headings */
.section-title{font-family:'Montserrat',sans-serif;font-weight:600;font-size:32px;text-align:center;letter-spacing:1px;color:#666}
.section-title b{color:var(--purple);font-weight:600}
.divider{display:block;margin:10px auto 0}
/* about */
.about{top:650px;height:388px;text-align:center}
.about .section-title{margin-top:62px}
.about p{width:814px;margin:24px auto 0;font-size:15px;line-height:29px;color:#666}
.btn-outline{display:inline-block;margin-top:30px;border:2px solid var(--purple);color:var(--purple);font-family:'Montserrat',sans-serif;font-weight:600;font-size:15px;width:170px;height:43px;line-height:39px}
/* why */
.why{top:1038px;height:409px}
.why-text{position:absolute;left:0;top:0;width:454px;height:409px;background:var(--grey-panel);color:var(--white);padding:84px 0 0 131px}
.why-text h3{font-family:'Montserrat',sans-serif;font-weight:500;font-size:25px}
.why-text p{font-size:14px;line-height:25px;margin-top:16px;width:300px}
.btn-ghost{display:inline-block;margin-top:24px;border:2px solid var(--white);font-size:14px;width:132px;height:37px;line-height:33px;text-align:center}
.why-photo{position:absolute;left:454px;top:0;width:746px;height:409px;background:linear-gradient(120deg,#dfe1e4 0%,#8c98a8 35%,#3c4658 60%,#b8a86a 85%,#e2e2e2 100%)}
/* services */
.services{top:1447px;height:397px;background:linear-gradient(110deg,#a772cf 0%,#7a3fb0 45%,#3a1270 75%,#2b0b55 100%);color:var(--white);text-align:center}
.services .section-title{color:var(--white);margin-top:44px}
.service-list{position:absolute;top:142px;left:0;width:1200px}
.service{position:absolute;width:260px;text-align:center}
.service svg{display:block;margin:0 auto}
.service span{display:block;margin-top:18px;font-size:16px;line-height:23px;text-transform:uppercase;opacity:.9}
/* projects */
.projects{top:1844px;height:517px;background:var(--grey-bg)}
.projects .section-title{margin-top:40px}
.card{position:absolute;top:120px;width:310px;height:325px;background:var(--white);text-align:center;box-shadow:0 1px 3px rgba(0,0,0,.12)}
.card .thumb{height:188px}
.card h4{font-weight:400;font-size:20px;color:#444;margin-top:18px}
.card p{font-size:13px;line-height:19px;color:#555;margin:10px auto 0;width:230px}
.card .more{font-size:12px;font-weight:700;color:#333;margin-top:6px;display:block}
.arrow{position:absolute;top:252px}
/* contact */
.contact{top:2361px;height:349px;background:linear-gradient(90deg,#3a4149 0%,#4f5860 40%,#3f4a58 70%,#2e3a4a 100%);color:var(--white);text-align:center}
.contact .section-title{color:var(--white);margin-top:82px}
.contact p{font-size:19px;line-height:26px;margin:18px auto 0;width:720px}
.btn-white{display:inline-block;margin-top:22px;border:2px solid var(--white);font-size:15px;width:152px;height:41px;line-height:37px}
/* footer */
.site-footer{top:2710px;height:295px;background:var(--dark);color:#ddd}
.site-footer .brand{position:absolute;left:119px;top:108px;color:var(--white)}
.foot-col{position:absolute;top:68px}
.foot-col h5{font-family:'Montserrat',sans-serif;font-weight:600;font-size:16px;color:var(--white);letter-spacing:1px;margin-bottom:12px}
.foot-col li{list-style:none;font-size:14px;line-height:31px}
.foot-col li svg{vertical-align:-2px;margin-right:8px}
.socials{display:flex;gap:8px;margin-top:10px}
.socials span{width:32px;height:32px;border:2px solid #ddd;border-radius:50%}
.copyright{position:absolute;top:3005px;left:0;width:1200px;height:61px;background:var(--darker);color:#bbb;font-size:14px;text-align:center;line-height:61px}
</style>
</head>
<body>

<header class="site-header">
  <div class="brand">K7 Electrical<br>Services Ltd</div>
  <div class="phone">
    <svg width="18" height="18" viewBox="0 0 24 24"><path fill="#5b2d8e" d="M6.6 10.8a15 15 0 0 0 6.6 6.6l2.2-2.2c.3-.3.7-.4 1-.2 1.1.4 2.3.6 3.6.6.6 0 1 .4 1 1V20c0 .6-.4 1-1 1A17 17 0 0 1 3 4c0-.6.4-1 1-1h3.5c.6 0 1 .4 1 1 0 1.3.2 2.5.6 3.6.1.3 0 .7-.2 1z"/></svg>
    (555) 014 2290
  </div>
  <nav class="main-nav">
    <a class="active">HOME</a><a>ABOUT US</a><a>SERVICES</a><a>PROJECTS</a><a>WHY US</a><a>CONTACT</a>
  </nav>
</header>

<section class="hero" role="img" aria-label="Electrician in a hard hat cutting wires at a wall panel">
  <h1>ELECTRICAL CONTRACTING AND</h1>
  <h2>DESIGN AND MAINTENANCE</h2>
  <a class="btn-orange">CONTACT US</a>
  <div class="dots"><span></span><span></span><span></span><span></span></div>
</section>

<section class="about">
  <h2 class="section-title">ABOUT <b>K7 ELECTRICAL</b></h2>
  <svg class="divider" width="220" height="10"><line x1="0" y1="5" x2="220" y2="5" stroke="#5b2d8e" stroke-width="2"/><circle cx="110" cy="5" r="5" fill="#5b2d8e"/></svg>
  <p>Vivamus porttitor purus nisi eleifend libero a tempus libero lectus feugiat felis Morbi diam mauris viverra in gravida eu mattis in ante Morbi eget arcu Morbi porta libero id ullamcorper nonummy nibh ligula pulvinar metus eget consectetuer augue nisi quis lacus Ut ac mi quis lacus mollis aliquam Curabitur iaculis tempus eros Curabitur vel mi sit amet magna malesuada ultrices Ut nisi erat fermentum vel congue id euismod in elit</p>
  <a class="btn-outline">READ MORE</a>
</section>

<section class="why">
  <div class="why-text">
    <h3>WHY WE ARE</h3>
    <p>Vivamus porttitor purus nisi eleifend libero a tempus libero lectus feugiat felis Morbi diam mauris viverra in gravida eu mattis in ante Morbi eget arcu Morbi porta libero id ullamcorper nonummy nibh</p>
    <a class="btn-ghost">READ MORE</a>
  </div>
  <div class="why-photo" role="img" aria-label="Electrician in a hard hat checking plans at a distribution board"></div>
</section>

<section class="services">
  <h2 class="section-title">SERVICES PROVIDE</h2>
  <svg class="divider" width="220" height="10"><line x1="0" y1="5" x2="220" y2="5" stroke="#fff" stroke-width="2"/><circle cx="110" cy="5" r="5" fill="#fff"/></svg>
  <div class="service-list">
    <div class="service" style="left:91px">
      <svg width="106" height="96" viewBox="0 0 106 96"><polygon points="27,2 79,2 104,48 79,94 27,94 2,48" fill="none" stroke="rgba(255,255,255,.6)" stroke-width="2"/><g fill="none" stroke="#fff" stroke-width="2.5"><path d="M38 36h30M44 36v-8M62 36v-8M40 36v8a13 13 0 0 0 26 0v-8M53 57v10h-12"/></g></svg>
      <span>Electrical<br>Installations</span>
    </div>
    <div class="service" style="left:342px">
      <svg width="106" height="96" viewBox="0 0 106 96"><polygon points="27,2 79,2 104,48 79,94 27,94 2,48" fill="none" stroke="rgba(255,255,255,.6)" stroke-width="2"/><g fill="none" stroke="#fff" stroke-width="2.5"><rect x="38" y="33" width="30" height="30" rx="5"/><rect x="33" y="28" width="30" height="30" rx="5"/><circle cx="48" cy="43" r="8"/></g></svg>
      <span>Design and<br>Maintenance</span>
    </div>
    <div class="service" style="left:596px">
      <svg width="106" height="96" viewBox="0 0 106 96"><polygon points="27,2 79,2 104,48 79,94 27,94 2,48" fill="none" stroke="rgba(255,255,255,.6)" stroke-width="2"/><g fill="none" stroke="#fff" stroke-width="2.5"><rect x="42" y="26" width="22" height="40" rx="3"/><rect x="46" y="31" width="14" height="9"/><circle cx="53" cy="53" r="5"/><path d="M42 40h-8v14M64 40h8v14"/></g></svg>
      <span>Residential and<br>Commercial Upgrading</span>
    </div>
    <div class="service" style="left:845px">
      <svg width="106" height="96" viewBox="0 0 106 96"><polygon points="27,2 79,2 104,48 79,94 27,94 2,48" fill="none" stroke="rgba(255,255,255,.6)" stroke-width="2"/><g fill="none" stroke="#fff" stroke-width="2.5"><path d="M33 45l20-18 20 18v22H33z"/><circle cx="53" cy="47" r="7"/><path d="M50 55v4h6v-4"/></g></svg>
      <span>Lighting Design and<br>Application</span>
    </div>
  </div>
</section>

<section class="projects">
  <h2 class="section-title"><b>OUR PROJECTS</b></h2>
  <svg class="divider" width="220" height="10"><line x1="0" y1="5" x2="220" y2="5" stroke="#5b2d8e" stroke-width="2"/><circle cx="110" cy="5" r="5" fill="#5b2d8e"/></svg>
  <svg class="arrow" style="left:80px" width="20" height="34" viewBox="0 0 20 34"><path d="M17 2L3 17l14 15" fill="none" stroke="#888" stroke-width="3"/></svg>
  <svg class="arrow" style="left:1096px" width="20" height="34" viewBox="0 0 20 34"><path d="M3 2l14 15L3 32" fill="none" stroke="#888" stroke-width="3"/></svg>
  <div class="card" style="left:117px">
    <div class="thumb" role="img" aria-label="Circuit breakers mounted in a panel" style="background:linear-gradient(135deg,#e9ecef,#b9c0c8)"></div>
    <h4>Project Title here</h4>
    <p>Ut nisi erat fermentum vel congue id euismod in elit Fusce ultricies orci</p>
    <span class="more">READ MORE</span>
  </div>
  <div class="card" style="left:442px">
    <div class="thumb" role="img" aria-label="Worker fitting a ceiling unit" style="background:linear-gradient(135deg,#3a3f46,#9aa3ad)"></div>
    <h4>Project Title here</h4>
    <p>Ut nisi erat fermentum vel congue id euismod in elit Fusce ultricies orci</p>
    <span class="more">READ MORE</span>
  </div>
  <div class="card" style="left:769px">
    <div class="thumb" role="img" aria-label="Pendant lamps glowing warm" style="background:linear-gradient(135deg,#2a1d12,#b5742c 55%,#3a2a1c)"></div>
    <h4>Project Title here</h4>
    <p>Ut nisi erat fermentum vel congue id euismod in elit Fusce ultricies orci</p>
    <span class="more">READ MORE</span>
  </div>
</section>

<section class="contact" role="img" aria-label="Electrician working on a switchboard, darkened background">
  <h2 class="section-title">CONTACT US NOW</h2>
  <svg class="divider" width="220" height="10"><line x1="0" y1="5" x2="220" y2="5" stroke="#fff" stroke-width="2"/><circle cx="110" cy="5" r="5" fill="#fff"/></svg>
  <p>Ut nisi erat fermentum vel congue id euismod in elit Fusce ultricies orci ac feugiat suscipit leo massa sodales velit et scelerisque mi tortor</p>
  <a class="btn-white">CLICK HERE</a>
</section>

<footer class="site-footer">
  <div class="brand">K7 Electrical<br>Services Ltd</div>
  <div class="foot-col" style="left:409px">
    <h5>QUICK LINKS</h5>
    <ul><li>About Us</li><li>Why Us</li><li>Services</li><li>Contact Us</li></ul>
  </div>
  <div class="foot-col" style="left:589px">
    <h5>SERVICES</h5>
    <ul><li>Electrical installations</li><li>Design and maintenance</li><li>Commercial upgrading</li><li>Lighting design</li></ul>
  </div>
  <div class="foot-col" style="left:814px">
    <h5>CONTACT US</h5>
    <ul>
      <li><svg width="12" height="14" viewBox="0 0 12 16"><path fill="#ddd" d="M6 0a6 6 0 0 0-6 6c0 4.5 6 10 6 10s6-5.5 6-10a6 6 0 0 0-6-6zm0 8.5A2.5 2.5 0 1 1 6 3.5a2.5 2.5 0 0 1 0 5z"/></svg>482 Harlow Avenue, Austin TX 78701</li>
      <li><svg width="14" height="14" viewBox="0 0 24 24"><path fill="#ddd" d="M6.6 10.8a15 15 0 0 0 6.6 6.6l2.2-2.2c.3-.3.7-.4 1-.2 1.1.4 2.3.6 3.6.6.6 0 1 .4 1 1V20c0 .6-.4 1-1 1A17 17 0 0 1 3 4c0-.6.4-1 1-1h3.5c.6 0 1 .4 1 1 0 1.3.2 2.5.6 3.6.1.3 0 .7-.2 1z"/></svg>555.014.2290</li>
      <li><svg width="14" height="12" viewBox="0 0 16 12"><rect x="1" y="1" width="14" height="10" fill="none" stroke="#ddd" stroke-width="1.5"/><path d="M1 1l7 6 7-6" fill="none" stroke="#ddd" stroke-width="1.5"/></svg>info@k7electrical.com</li>
    </ul>
    <div class="socials"><span></span><span></span><span></span><span></span></div>
  </div>
</footer>

<div class="copyright">© 2018 K7 Electrical Services Ltd&nbsp; All right reserved</div>

</body>
</html>
```